Brightfield Homes needs a web design and brand identifier

Brightfield Homes is a pioneering approach by Victorian councils and four greenhouse alliances to support low income households to install solar systems with no upfront costs.

Brightfield Homes will commence in May 2017.

Brightfield Homes is looking for a designer to create a website banner incorporating a brand identifier for Brightfield Homes. The brand identifier will be used in Brightfield Homes promotional materials, such as flyers and mail outs.

The website banner and brand identifier should engender trust and confidence in the target group (retirees).

Reason: Hi, Thank you for your work so far. We've been given advice to get a separate logo designed (instead of trying to include this as part of the banner design). Sorry for not realising this until now - we're new to all this. So, I have a couple of preliminary logo designs that are being considered by our project control group. I will forward a copy of the logo once we have it. The project control group is looking for a web design that is unique to Brightfield Homes and a design that draws on the key elements of the program (i.e. it helps people save money and take control). The site should be friendly but not too informal as the target group is seniors. Here's a link to another community energy organisation: www.kindlewattnet.com.au/ Apologies again for the delays. Cheers, Doug

Target Market(s)

Home owning, low income, retirees

Industry/Entity Type

Non Profit

Number of Pages Required

1 page

Font styles to use
Sans Serif

Requirements
Must have
• Use of Brightfield Home name
• Must promote Brightfield Homes as safe, reliable and trustworthy
Nice to have
• Blue - to engender sense of safety and confidence (open to suggestions, though)
• Solar panels / the sun
Should not have
• Anything that is hard to read
• anything that promotes riskyness

```html
<!DOCTYPE html>
<html lang="en">
<head>
<meta charset="utf-8">
<title>Brightfield Homes</title>
<link href="https://fonts.googleapis.com/css2?family=Titillium+Web:wght@400;600;700&family=Open+Sans:wght@400;600;700&display=swap" rel="stylesheet">
<style>
:root{
  --blue:#2f8ad8;
  --blue-deep:#2474c0;
  --navy:#253447;
  --red:#e8503f;
  --orange:#f39324;
  --yellow:#f8b62a;
  --grey-bg:#e9e9e9;
  --light:#f1f1f1;
  --text:#444b55;
  --white:#ffffff;
}
*{box-sizing:border-box;margin:0;padding:0}
html,body{width:1200px;height:2769px;overflow:hidden}
body{font-family:"Open Sans",Arial,sans-serif;color:var(--text);background:var(--white);position:relative}
.heading{font-family:"Titillium Web",Arial,sans-serif;font-weight:700;text-transform:uppercase}
section,header,footer{position:absolute;left:0;width:1200px}
.abs{position:absolute}

/* header + hero */
.hero{top:0;height:600px;background:linear-gradient(110deg,#4f6a2e 0%,#7b8d45 30%,#a8895c 55%,#c9a27c 70%,#6f7f3f 100%)}
.hero-photo{position:absolute;inset:0}
.site-header{top:0;height:96px;background:rgba(20,28,38,.55);z-index:2}
.brand-tab{position:absolute;left:0;top:0;width:443px;height:96px}
.brand-name{position:absolute;left:172px;top:26px;font-family:"Titillium Web",sans-serif;font-weight:700;font-size:33px;color:var(--white);letter-spacing:.5px}
.call{position:absolute;left:682px;top:8px;color:var(--white);display:flex;align-items:center;gap:10px}
.call small{display:block;font-size:10px;font-weight:600;letter-spacing:.5px}
.call strong{display:block;font-family:"Titillium Web",sans-serif;font-size:24px;font-weight:600;line-height:24px}
.quote-btn{position:absolute;left:888px;top:17px;width:138px;height:30px;border-radius:15px;background:var(--red);color:var(--white);font-size:11px;font-weight:700;text-align:center;line-height:30px}
.nav{position:absolute;right:172px;top:68px;display:flex;gap:28px;font-size:11px;font-weight:700;color:var(--white)}
.hero-panel{position:absolute;left:100px;top:108px;width:560px;height:440px;z-index:1}
.hero-copy{position:absolute;left:172px;top:240px;width:420px;color:var(--white);z-index:3}
.hero-kicker{font-family:"Titillium Web",sans-serif;font-size:23px;font-weight:400;text-transform:uppercase;letter-spacing:.5px}
.hero-title{font-size:60px;line-height:56px;margin-top:-2px}
.hero-text{font-size:16px;line-height:27px;margin-top:26px}
.hero-phone{display:flex;align-items:center;gap:12px;margin-top:18px;font-family:"Titillium Web",sans-serif;font-size:27px}

/* welcome */
.welcome{top:600px;height:447px;background:var(--white)}
.section-title{position:absolute;left:0;width:1200px;text-align:center;font-size:33px;color:#1d232b}
.rule{position:absolute;left:575px;width:50px;height:3px;background:var(--blue)}
.video{position:absolute;left:172px;top:146px;width:428px;height:240px;background:linear-gradient(180deg,#7a9a9c 0%,#8fb2a8 55%,#6aa08f 100%)}
.play{position:absolute;left:184px;top:88px;width:60px;height:60px;border:3px solid var(--white);border-radius:50%}
.play:after{content:"";position:absolute;left:22px;top:15px;border-left:20px solid var(--white);border-top:12px solid transparent;border-bottom:12px solid transparent}
.video span{position:absolute;left:0;width:428px;top:160px;text-align:center;color:var(--white);font-size:11px;font-weight:700}
.welcome-text{position:absolute;left:633px;top:146px;width:370px;font-size:14px;line-height:22px}
.welcome-text p+p{margin-top:22px}

/* how it works */
.how{top:1047px;height:476px;background:var(--navy)}
.how .section-title{top:48px;color:var(--white);font-size:27px}
.steps{position:absolute;left:172px;top:127px;display:flex;gap:22px}
.step{position:relative;width:198px;height:288px;border-radius:6px;background:linear-gradient(160deg,var(--yellow) 0%,var(--orange) 100%);text-align:center;color:var(--white)}
.step:nth-child(2){background:linear-gradient(160deg,#f7ab2a,#f28a22)}
.step:nth-child(3){background:linear-gradient(160deg,#f59f27,#ef7f22)}
.step:nth-child(4){background:linear-gradient(160deg,#f39324,#ed7a21)}
.step-num{position:absolute;left:18px;top:-4px;width:30px;height:30px;border-radius:50%;background:var(--red);color:var(--white);font-family:"Titillium Web",sans-serif;font-size:15px;font-weight:600;line-height:30px}
.step-icon{margin:22px auto 0;width:118px;height:118px;border-radius:50%;border:7px solid var(--white);background:radial-gradient(circle,#fcd14a 0%,#f7a62a 100%)}
.step p{font-size:12px;line-height:20px;padding:22px 22px 0}

/* eligibility */
.eligible{top:1523px;height:578px;background:var(--grey-bg)}
.who-photo{position:absolute;left:611px;top:0;width:589px;height:578px;background:linear-gradient(180deg,#1f7fd2 0%,#4a9fe0 35%,#3c5f8e 55%,#c7562c 78%,#e3743a 100%)}
.leaf{position:absolute;display:flex;align-items:center;justify-content:center;text-align:center;color:var(--white);font-size:12px;font-weight:700;line-height:16px;border-radius:4px 40px 4px 40px;padding:0 16px;box-shadow:inset 0 0 0 4px rgba(255,255,255,.15)}
.leaf-owner{left:172px;top:89px;width:197px;height:197px;background:var(--navy);border-radius:40px 4px 40px 4px}
.leaf-pension{left:384px;top:44px;width:197px;height:181px;background:var(--blue)}
.leaf-home{left:172px;top:301px;width:197px;height:188px;background:var(--blue-deep)}
.leaf-usage{left:399px;top:338px;width:195px;height:179px;background:var(--red);border-radius:40px 4px 40px 4px}
.eligible-title{position:absolute;left:425px;top:240px;font-size:26px;line-height:27px;color:#1d232b}
.eligible-sub{position:absolute;left:425px;top:300px;font-size:12px;color:#666}
.who-copy{position:absolute;left:646px;top:50px;width:380px;color:var(--white)}
.who-copy h2{font-size:31px;line-height:34px}
.who-copy p{font-size:13px;line-height:21px;margin-top:10px}

/* what next */
.next{top:2101px;height:175px;background:var(--red);color:var(--white);text-align:center}
.next h2{position:absolute;top:30px;width:1200px;font-size:26px}
.next .rule{background:var(--white);top:72px}
.next p{position:absolute;top:92px;width:1200px;font-size:14px}
.next .contact{top:120px;font-family:"Titillium Web",sans-serif;font-size:25px;font-weight:700}

/* partners */
.partners{top:2276px;height:229px;background:var(--light)}
.partners h2{position:absolute;top:40px;width:1200px;text-align:center;font-size:18px;color:#1d232b}
.partner-row{position:absolute;left:218px;top:100px;display:flex;gap:64px;align-items:center}
.partner{background:#bfc1c4;border-radius:6px}

/* footer */
.site-footer{top:2505px;height:264px;background:var(--blue);color:var(--white)}
.col{position:absolute;top:28px;font-size:11px;line-height:22px}
.col h3{font-family:"Open Sans",sans-serif;font-size:12px;font-weight:700;margin-bottom:8px}
.contact-item{display:flex;gap:10px;margin-bottom:10px;line-height:16px}
.socials{display:flex;gap:12px}
.socials span{width:22px;height:22px;border:2px solid var(--white);border-radius:50%}
.field{width:196px;height:28px;background:var(--blue-deep);border:1px solid #5fa7e6;padding:0 8px;line-height:26px;margin-bottom:8px}
.join{width:196px;height:30px;background:var(--red);text-align:center;line-height:30px;font-weight:700}
.copyright{position:absolute;left:172px;top:240px;font-size:10px}
</style>
</head>
<body>

<section class="hero">
  <div class="hero-photo" role="img" aria-label="Photo of a smiling senior man in a straw hat leaning on a garden fence"></div>
  <svg class="hero-panel" viewBox="0 0 560 440" aria-hidden="true">
    <path d="M10 20 C120 -10 260 50 400 10 C470 -5 520 10 545 20 C520 120 560 220 530 330 C510 380 540 420 540 430 C420 400 300 460 160 420 C90 400 40 430 15 420 C30 300 -10 180 25 110 Z" fill="#2f8ad8" transform="translate(8 6)"/>
    <path d="M10 20 C120 -10 260 50 400 10 C470 -5 520 10 545 20 C520 120 560 220 530 330 C510 380 540 420 540 430 C420 400 300 460 160 420 C90 400 40 430 15 420 C30 300 -10 180 25 110 Z" fill="#e8503f"/>
  </svg>
  <div class="hero-copy">
    <div class="hero-kicker">Help pensioner households to</div>
    <h1 class="heading hero-title">Save Money</h1>
    <p class="hero-text">and take control of their energy bills by installing an affordable, quality solar system and be part of an Australian first</p>
    <div class="hero-phone">
      <svg width="24" height="24" viewBox="0 0 24 24" aria-hidden="true"><path d="M6.5 2.5l3 4-2 2.5c1.2 2.6 3.3 4.7 6 6l2.5-2 4 3-2 4.5C10 20 4 14 2 4.5z" fill="none" stroke="#fff" stroke-width="1.6" stroke-linejoin="round"/></svg>
      0400 555 123
    </div>
  </div>
</section>

<header class="site-header">
  <svg class="brand-tab" viewBox="0 0 443 96" aria-hidden="true"><path d="M0 0H443L400 96H0Z" fill="#2f8ad8"/></svg>
  <div class="brand-name">BRIGHTFIELD HOMES</div>
  <div class="call">
    <svg width="26" height="26" viewBox="0 0 24 24" aria-hidden="true"><path d="M6.5 2.5l3 4-2 2.5c1.2 2.6 3.3 4.7 6 6l2.5-2 4 3-2 4.5C10 20 4 14 2 4.5z" fill="none" stroke="#fff" stroke-width="1.6" stroke-linejoin="round"/></svg>
    <div><small>CALL NOW</small><strong>0400 555 123</strong></div>
  </div>
  <div class="quote-btn">REQUEST A QUOTE</div>
  <nav class="nav"><span>HOME</span><span>ABOUT US</span><span>SERVICES</span><span>HOW IT WORKS</span><span>CONTACT US</span></nav>
</header>

<section class="welcome">
  <h2 class="heading section-title" style="top:56px">Welcome to Brightfield Homes</h2>
  <div class="rule" style="top:106px"></div>
  <div class="video" role="img" aria-label="Video still: illustrated landscape with solar panels, wind turbines and a small house">
    <div class="play"></div><span>WATCH VIDEO</span>
  </div>
  <div class="welcome-text">
    <p>We need you Help pensioner households to save money and take control of their energy bills by installing an affordable, quality solar system and be part of an Australian first.</p>
    <p>Brightfield Homes is a pioneering approach by Victorian councils to support pensioner households to install solar with no upfront costs. We’ve done the hard work of finding a safe, reliable and quality installer so pensioners don’t have to.</p>
  </div>
</section>

<section class="how">
  <h2 class="heading section-title">How it works</h2>
  <div class="rule" style="top:94px"></div>
  <div class="steps">
    <div class="step"><div class="step-num">01</div><div class="step-icon" role="img" aria-label="Icon of a sun with a plug"></div><p>Brightfield Homes checks that every person gets a solar system that pays for itself in energy savings from day one</p></div>
    <div class="step"><div class="step-num">02</div><div class="step-icon" role="img" aria-label="Icon of a solar panel and battery"></div><p>Brightfield Homes organises for the solar system to be installed</p></div>
    <div class="step"><div class="step-num">03</div><div class="step-icon" role="img" aria-label="Icon of a senior with a walking stick"></div><p>Brightfield Homes supports pensioners to understand and get the most out of solar</p></div>
    <div class="step"><div class="step-num">04</div><div class="step-icon" role="img" aria-label="Icon of a solar panel marked zero percent"></div><p>Pensioners gradually pay for cost through their usual rates payments at 0% interest</p></div>
  </div>
</section>

<section class="eligible">
  <div class="leaf leaf-owner">HOMEOWNERS</div>
  <div class="leaf leaf-pension">PENSION CARD<br>HOLDERS</div>
  <div class="leaf leaf-home">USUALLY AT HOME<br>FROM 9AM TO 5PM</div>
  <div class="leaf leaf-usage">AVERAGE TO HIGH<br>ELECTRICITY USERS</div>
  <h2 class="heading eligible-title">Is my client<br>eligible?</h2>
  <div class="eligible-sub">Refer clients who are:</div>
  <div class="who-photo" role="img" aria-label="Photo of solar panels on a terracotta tiled roof under a bright blue sky"></div>
  <div class="who-copy">
    <h2 class="heading">Who is Brightfield Homes?</h2>
    <p>Over 20 Victorian councils have come together with support from the State Government’s Clean Energy Jobs Fund to run the Brightfield Home program.</p>
  </div>
</section>

<section class="next">
  <h2 class="heading">What next?</h2>
  <div class="rule"></div>
  <p>To refer clients or for further information, contact Doug Hartley at Brightfield Homes:</p>
  <p class="contact">Call us : 0400 555 123 &nbsp;|&nbsp; Email us : doug.hartley@northvale.vic.gov.au</p>
</section>

<section class="partners">
  <h2 class="heading">Brightfield Homes is a partnership between</h2>
  <div class="partner-row">
    <div class="partner" style="width:150px;height:80px;border-radius:50%"></div>
    <div class="partner" style="width:190px;height:60px"></div>
    <div class="partner" style="width:170px;height:60px"></div>
    <div class="partner" style="width:110px;height:70px;border-radius:50%"></div>
  </div>
</section>

<footer class="site-footer">
  <div class="col" style="left:172px"><h3>QUICK LINKS</h3>Home<br>About Us<br>Services<br>How It Works<br>Contact Us</div>
  <div class="col" style="left:295px"><h3>SUPPORT</h3>Contact us<br>FAQs<br>Legal<br>Privacy Policy<br>Legal</div>
  <div class="col" style="left:415px;width:220px"><h3>CONTACT US</h3>
    <div class="contact-item"><svg width="22" height="22" viewBox="0 0 22 22" aria-hidden="true"><circle cx="11" cy="11" r="10" fill="#fff"/><path d="M11 5a4 4 0 0 0-4 4c0 3 4 7 4 7s4-4 4-7a4 4 0 0 0-4-4z" fill="#2f8ad8"/></svg><div>Your Company LTD.<br>Street Name, 000000<br>City Name</div></div>
    <div class="contact-item"><svg width="22" height="22" viewBox="0 0 22 22" aria-hidden="true"><circle cx="11" cy="11" r="10" fill="#fff"/><path d="M8 5.5l2 2.5-1.2 1.5c.8 1.6 2 2.8 3.6 3.6l1.4-1.2 2.5 2-1.2 2.6C10 16 6 12 5.5 7z" fill="#2f8ad8"/></svg><div>Phone<br>0400 555 123</div></div>
    <div class="contact-item"><svg width="22" height="22" viewBox="0 0 22 22" aria-hidden="true"><circle cx="11" cy="11" r="10" fill="#fff"/><rect x="6" y="7.5" width="10" height="7" fill="#2f8ad8"/><path d="M6 7.5l5 4 5-4" fill="none" stroke="#fff" stroke-width="1"/></svg><div>Email<br>doug.hartley@northvale.vic.gov.au</div></div>
  </div>
  <div class="col" style="left:648px"><h3>GET CONNECTED</h3><div class="socials"><span></span><span></span><span></span><span></span></div></div>
  <div class="col" style="left:831px"><h3>E-NEWSLETTER SIGNUP</h3><div class="field">Name</div><div class="field">Email</div><div class="join">JOIN</div></div>
  <div class="copyright">© 2017 Brightfield Homes. All Rights Reserved</div>
</footer>

</body>
</html>
```